Business card for Luxury Portable Restroom Trailer company

We are a Luxury Portable Restroom Trailer Company Called FALCRIDGE HIRES. Based in Orange County California. We provide portable restroom trailers for events, such as, Weddings, Concerts, Charity events, Sporting events, Tournaments, Corporate events, ect. We rent and Sell the Luxury restrooms. Our colors are white, grey, and Orange. As you will see in the logo we uploaded.
There are 2 people in the company so the names and titles will change for the 3 people but card will remain the same. Here is the information for each Person: Dwight Penner CFO 555 318-0476
next Person: Leon Marchetti VP 555 318-0476
Next Person: Owen Marchetti CEO 555 318-0476
Information to include on the card: Luxury Restroom Trailers Rental and Sales. Weddings, Concerts, Charity, Sporting and Corp. Events.

```html
<!DOCTYPE html>
<html lang="en">
<head>
<meta charset="UTF-8">
<title>Falcridge Hires – Business Card</title>
<link rel="stylesheet" href="https://fonts.googleapis.com/css2?family=Archivo:wght@400;500;800&display=swap">
<style>
  :root {
    --bg: #e4e4e6;
    --card: #4a4a4d;
    --white: #ffffff;
    --orange: #ec6420;
    --rule: #8c8c90;
    --text-soft: #f1f1f1;
  }
  * { box-sizing: border-box; margin: 0; padding: 0; }
  html, body { width: 1200px; height: 800px; overflow: hidden; }
  body {
    background: var(--bg);
    font-family: "Archivo", Arial, sans-serif;
    display: flex;
    align-items: center;
    justify-content: center;
    gap: 50px;
  }
  .card {
    position: relative;
    width: 540px;
    height: 310px;
    background: var(--card);
    border-radius: 22px;
    box-shadow: 0 4px 0 var(--orange), 0 18px 30px rgba(0,0,0,.22);
    color: var(--white);
  }

  /* contact side */
  .brand {
    display: flex;
    align-items: center;
    gap: 10px;
    font-weight: 800;
    letter-spacing: .04em;
    color: var(--white);
    white-space: nowrap;
  }
  .brand-dot { background: var(--orange); flex: none; }
  .card--contact .brand {
    position: absolute;
    top: 46px;
    right: 40px;
    font-size: 26px;
  }
  .card--contact .brand-dot { width: 14px; height: 14px; }

  .divider {
    position: absolute;
    left: 34px;
    right: 34px;
    top: 200px;
    height: 1px;
    background: var(--rule);
  }
  .person {
    position: absolute;
    left: 40px;
    top: 146px;
  }
  .person-name {
    font-size: 22px;
    font-weight: 500;
    color: var(--orange);
    line-height: 1.1;
  }
  .person-title {
    font-size: 14px;
    color: var(--text-soft);
    margin-top: 3px;
  }
  .address {
    position: absolute;
    left: 40px;
    top: 214px;
    font-size: 14px;
    line-height: 1.45;
    color: var(--text-soft);
  }
  .contact {
    position: absolute;
    right: 40px;
    font-size: 14px;
    line-height: 1.45;
    color: var(--text-soft);
    list-style: none;
    text-align: right;
  }
  .contact--phone { top: 174px; }
  .contact--online { top: 214px; }
  .contact li { display: flex; align-items: center; justify-content: flex-end; gap: 8px; }
  .contact svg { width: 12px; height: 12px; fill: var(--orange); flex: none; }

  /* brand side */
  .card--brand {
    display: flex;
    flex-direction: column;
    align-items: center;
    justify-content: center;
  }
  .card--brand .brand { font-size: 40px; gap: 14px; }
  .card--brand .brand-dot { width: 20px; height: 20px; }
  .tagline {
    margin-top: 34px;
    text-align: center;
    font-size: 15px;
    line-height: 1.5;
    color: var(--text-soft);
  }
</style>
</head>
<body>

  <section class="card card--contact" aria-label="Contact side">
    <div class="brand"><span class="brand-dot"></span>FALCRIDGE HIRES</div>

    <div class="person">
      <p class="person-name">Dwight Penner</p>
      <p class="person-title">CFO</p>
    </div>

    <ul class="contact contact--phone">
      <li>555 318-0476
        <svg viewBox="0 0 24 24" aria-hidden="true"><path d="M6.6 10.8a15.1 15.1 0 0 0 6.6 6.6l2.2-2.2a1 1 0 0 1 1-.25 11.4 11.4 0 0 0 3.6.57 1 1 0 0 1 1 1V20a1 1 0 0 1-1 1A17 17 0 0 1 3 4a1 1 0 0 1 1-1h3.5a1 1 0 0 1 1 1c0 1.25.2 2.45.57 3.57a1 1 0 0 1-.25 1z"/></svg>
      </li>
    </ul>

    <div class="divider"></div>

    <p class="address">2170 Harbor Crest Drive<br>Tustin, CA 92780</p>

    <ul class="contact contact--online">
      <li>name@falcridge.com
        <svg viewBox="0 0 24 24" aria-hidden="true"><path d="M2 5h20v14H2z M2 5l10 8 10-8" fill="var(--orange)"/><path d="M3 6l9 7 9-7" fill="none" stroke="#4a4a4d" stroke-width="1.6"/></svg>
      </li>
      <li>www.falcridge.com
        <svg viewBox="0 0 24 24" aria-hidden="true"><circle cx="12" cy="12" r="10"/><path d="M2 12h20M12 2c3 3 3 17 0 20M12 2c-3 3-3 17 0 20" fill="none" stroke="#4a4a4d" stroke-width="1.5"/></svg>
      </li>
    </ul>
  </section>

  <section class="card card--brand" aria-label="Brand side">
    <div class="brand"><span class="brand-dot"></span>FALCRIDGE HIRES</div>
    <p class="tagline">
      Luxury Restroom Trailers Rental and Sales<br>
      Weddings, Concerts, Charity, Sporting and Corp Events
    </p>
  </section>

</body>
</html>
```